Business Card for a New Zealand IT Startup

I need a business card for VELTA Holdings. We are a young startup based in New Zealand working in internet marketing and web development. The design should have some element connected to New Zealand, such as wave, koru or silver fern, just don't use a kiwi bird.

```html
<!DOCTYPE html>
<html lang="en">
<head>
<meta charset="utf-8">
<title>VELTA Holdings — Business Card</title>
<link href="https://fonts.googleapis.com/css2?family=Open+Sans:wght@400;600;700&display=swap" rel="stylesheet">
<style>
  :root {
    --backdrop: #5c5c5c;
    --brand-blue: #0a6fba;
    --brand-orange: #f15a24;
    --card-white: #ffffff;
    --card-shadow: rgba(0, 0, 0, 0.45);
  }
  * { box-sizing: border-box; margin: 0; padding: 0; }
  html, body {
    width: 1200px;
    height: 802px;
    overflow: hidden;
    background: var(--backdrop);
    font-family: "Open Sans", Arial, sans-serif;
  }
  .stage { position: relative; width: 1200px; height: 802px; }
  .card {
    position: absolute;
    top: 274px;
    width: 443px;
    height: 265px;
    overflow: hidden;
    box-shadow: 3px 4px 6px var(--card-shadow);
  }
  .card--front { left: 136px; background: var(--brand-blue); }
  .card--back { left: 624px; background: var(--card-white); }

  .front__band {
    position: absolute; left: 0; top: 0;
    width: 130px; height: 100%;
    background: var(--brand-orange);
  }
  .front__mark {
    position: absolute;
    left: -4px; top: 4px;
    width: 258px; height: 258px;
    border-radius: 50%;
    background: var(--card-white);
  }

  .front__details {
    position: absolute;
    right: 21px; top: 62px;
    text-align: right;
    color: var(--card-white);
  }
  .holder__name { font-size: 16px; font-weight: 600; line-height: 20px; letter-spacing: 0.2px; }
  .holder__role { font-size: 12.5px; font-weight: 400; line-height: 16px; }
  .contact { list-style: none; margin-top: 25px; }
  .contact__item {
    display: flex; justify-content: flex-end; align-items: center;
    gap: 3px; font-size: 12.5px; line-height: 16px;
  }
  .contact__icon { width: 10px; height: 10px; fill: var(--card-white); }
  .address { margin-top: 7px; font-size: 12.5px; line-height: 16px; font-style: normal; }

  .back__wordmark {
    position: absolute; left: 0; right: 0; top: 84px;
    text-align: center;
    color: var(--brand-blue);
    font-weight: 700;
  }
  .wordmark__primary { font-size: 62px; line-height: 66px; letter-spacing: 1px; }
  .wordmark__secondary { font-size: 19px; line-height: 26px; letter-spacing: 13px; margin-right: -13px; }
</style>
</head>
<body>
<main class="stage">
  <section class="card card--front">
    <div class="front__band"></div>
    <div class="front__mark" role="img" aria-label="Brand symbol area: orange wave spiral on a white disc"></div>
    <div class="front__details">
      <p class="holder__name">MARTEN HOLLIS</p>
      <p class="holder__role">Managing Director</p>
      <ul class="contact">
        <li class="contact__item">044-123 456 789
          <svg class="contact__icon" viewBox="0 0 10 10" aria-hidden="true"><path d="M0 4 Q5 0 10 4 L8 5 L7 3.5 L3 3.5 L2 5 Z M2 5.5 H8 V9 H2 Z"/></svg>
        </li>
        <li class="contact__item">044-123 456 789
          <svg class="contact__icon" viewBox="0 0 10 10" aria-hidden="true"><path d="M2.5 0 H7.5 V10 H2.5 Z M3.5 1.2 V7.8 H6.5 V1.2 Z"/></svg>
        </li>
        <li class="contact__item">info@webname.com
          <svg class="contact__icon" viewBox="0 0 10 10" aria-hidden="true"><path d="M0 2 H10 V8.5 H0 Z" /><path d="M0.5 2.5 L5 6 L9.5 2.5" stroke="#0a6fba" stroke-width="0.9" fill="none"/></svg>
        </li>
        <li class="contact__item">www.websitename.com
          <svg class="contact__icon" viewBox="0 0 10 10" aria-hidden="true"><circle cx="5" cy="5" r="5"/><path d="M3 3 Q5 2 6 4 Q5 6 3 5 Z M6 6.5 Q8 6 8 8 Z" fill="#0a6fba"/></svg>
        </li>
      </ul>
      <address class="address">12345, Address Goes Here<br>Country Name, 123456</address>
    </div>
  </section>

  <section class="card card--back">
    <div class="back__wordmark">
      <p class="wordmark__primary">VELTA</p>
      <p class="wordmark__secondary">HOLDINGS</p>
    </div>
  </section>
</main>
</body>
</html>
```